4D Cradle Glimpse Luxury Ultrasound Billboard

Design a HIGH-END, MODERN billboard for my private prenatal ultrasound studio, 4D Cradle Glimpse, located in Pace, Florida.
This billboard will be viewed by drivers traveling at highway speeds, so it must be extremely clean, simple, and readable within 6 seconds.
About My Business
4D Cradle Glimpse is a private prenatal ultrasound studio specializing in:
Highest technology 4D/HD Ultrasounds
Early Gender Determination
Pregnancy Confirmation
I have been serving families for nearly 10 years and is known for creating a memorable experience, not just an ultrasound appointment.
Design Style
I DO NOT want:
Flowers
Leaves
Swirls
Glitter
Hearts everywhere
Busy backgrounds
Generic maternity stock graphics
I DO want:
Modern
Luxury
Upscale
Clean
Professional
Eye-catching
Premium medical spa feel
Colors
Use colors from my logo:
LOGO Green ( or a deep green)
Black
White
Soft Gold accents
Images:
Incorporate my professional headshot in a clean, modern way, logo, and the ultrasound images
Text
Keep wording minimal.
Primary Headline ( OPEN TO IDEAS) :
EXAMPLES ( WOULD RATHER SOMETHING MORE CATCHY)
" ADVANCED IMAGING. UNFORGETTABLE MOMENTS"
"MEET YOUR BABY BEFORE BIRTH"
Under headline:
4D Ultrasound • Early Gender • Pregnancy Confirmation
Business Name:
4D Cradle Glimpse
Private Prenatal Ultrasound Studio
Phone Number:
850-471-5923
Important
This billboard must be readable in 5–6 seconds from a moving vehicle.
Less text is better.
The phone number and business name must be visible from a distance.
The design should feel like a premium brand that immediately tells expecting parents:
“This is where I go to see my baby.”
Files Provided
Official logo
Headshot
Ultrasound images
Don’t make this look like a medical office billboard.
Make it look like a luxury baby experience billboard. That’s what separates 4D Cradle Glimpse from hospitals, OB offices, and all the new studios popping up around you. The emotional connection is what gets moms to book. ❤️
Billboard Size - 10.6” x 36”

```html
<!DOCTYPE html>
<html lang="en">
<head>
<meta charset="UTF-8">
<title>4D Cradle Glimpse Billboard</title>
<link href="https://fonts.googleapis.com/css2?family=Inter:wght@600;700;800&display=swap" rel="stylesheet">
<style>
  :root {
    --bg-deep: #1b1f15;
    --bg-glow: #3a4630;
    --gold: #c4922a;
    --white: #ffffff;
    --black: #111111;
    --logo-green: #2f5a36;
    --skin-dark: #7a3326;
    --skin-light: #c9806b;
  }
  * { margin: 0; padding: 0; box-sizing: border-box; }
  html, body { width: 1200px; height: 375px; overflow: hidden; background: var(--bg-deep); }
  .billboard {
    position: relative;
    width: 1200px;
    height: 375px;
    overflow: hidden;
    font-family: "Inter", sans-serif;
    color: var(--white);
    background: radial-gradient(circle at 100% 0%, var(--bg-glow) 0%, rgba(58,70,48,0) 38%), var(--bg-deep);
  }
  .headshot {
    position: absolute;
    left: 48px;
    top: 34px;
    width: 200px;
    height: 341px;
    border-radius: 90px 90px 0 0;
    background: linear-gradient(180deg, #c9b28a 0%, #a88a66 28%, var(--logo-green) 55%, #24422a 100%);
  }
  .headline {
    position: absolute;
    left: 280px;
    top: 28px;
    font-weight: 800;
    font-size: 67px;
    line-height: 71px;
    letter-spacing: -0.5px;
    text-transform: uppercase;
    white-space: nowrap;
  }
  .headline .accent { color: var(--gold); }
  .services {
    position: absolute;
    left: 281px;
    top: 197px;
    width: 610px;
    font-weight: 600;
    font-size: 18.5px;
    letter-spacing: 0;
    white-space: nowrap;
  }
  .brand-card {
    position: absolute;
    left: 285px;
    top: 252px;
    width: 175px;
    height: 95px;
    background: var(--white);
    border-radius: 10px;
    display: flex;
    align-items: center;
    justify-content: center;
    text-align: center;
    padding: 0 14px;
  }
  .brand-name {
    color: var(--gold);
    font-weight: 700;
    font-size: 22px;
    line-height: 26px;
  }
  .phone {
    position: absolute;
    left: 498px;
    top: 267px;
    width: 373px;
    height: 65px;
    background: var(--gold);
    border-radius: 6px;
    display: flex;
    align-items: center;
    padding-left: 10px;
  }
  .phone-icon { width: 39px; height: 39px; flex: none; }
  .phone-number {
    margin-left: 14px;
    color: var(--black);
    font-weight: 700;
    font-size: 38px;
    letter-spacing: 0.5px;
    white-space: nowrap;
  }
  .scan-image {
    position: absolute;
    left: 948px;
    top: 27px;
    width: 229px;
    height: 255px;
    border-radius: 12px;
    background: radial-gradient(ellipse at 50% 40%, var(--skin-light) 0%, #a85a47 45%, var(--skin-dark) 100%);
  }
  .location {
    position: absolute;
    left: 979px;
    top: 305px;
    display: flex;
    align-items: center;
    gap: 8px;
    font-weight: 700;
    font-size: 17px;
    white-space: nowrap;
  }
  .location svg { width: 33px; height: 33px; }
</style>
</head>
<body>
  <main class="billboard">
    <div class="headshot" role="img" aria-label="Portrait of the studio owner in green scrubs holding an ultrasound probe"></div>

    <h1 class="headline">Meet your <span class="accent">baby</span><br>before birth</h1>

    <p class="services">4D ULTRASOUND • EARLY GENDER • PREGNANCY CONFIRMATION</p>

    <div class="brand-card">
      <span class="brand-name">4D Cradle Glimpse</span>
    </div>

    <div class="phone">
      <svg class="phone-icon" viewBox="0 0 40 40" aria-hidden="true">
        <rect width="40" height="40" rx="5" fill="#111111"/>
        <path d="M13 9c1-1 2.5-1 3.3.2l2.3 3.4c.6 1 .4 2.2-.4 3l-1.6 1.5c1.3 2.8 3.5 5 6.3 6.3l1.5-1.6c.8-.8 2-1 3-.4l3.4 2.3c1.2.8 1.2 2.3.2 3.3l-1.6 1.6c-1.6 1.6-4 2-6 1C16.7 26.5 13.5 23.3 11.4 16.6c-1-2-.6-4.4 1-6z" fill="none" stroke="#c4922a" stroke-width="2.2" stroke-linejoin="round"/>
      </svg>
      <span class="phone-number">850-471-5923</span>
    </div>

    <div class="scan-image" role="img" aria-label="4D ultrasound image of twin babies face to face"></div>

    <div class="location">
      <svg viewBox="0 0 34 34" aria-hidden="true">
        <circle cx="17" cy="17" r="17" fill="#c4922a"/>
        <path d="M17 8a6 6 0 0 0-6 6c0 4.5 6 11 6 11s6-6.5 6-11a6 6 0 0 0-6-6z" fill="#111111"/>
        <circle cx="17" cy="14" r="2" fill="#c4922a"/>
      </svg>
      <span>PACE, FLORIDA</span>
    </div>
  </main>
</body>
</html>
```